Business Card Design

Hi I need a business card designed, we already have the business name logo artwork and would like some concept ideas for the Bus Card layout.
On the back of the card i want to include the products and services that we offer.
We are a Plastics Sheeting manufacture based in Perth Australia.

                                       

We need a BC design for a company called Tarvo Plastics based in Perth Australia.

We supply from DIY to Trade & Industrial  Engineering Markets.

We specialise in:

·         Cut to size panels  (all shapes and sizes)

·         Plastics fabrication & Welding

·         Custom Designs

·         Plastic Repairs

·         PVC Pipe Slotting & PVC Pipe Threading

·         Supplier of all types of engineering plastics and profiles.

Including:           Acrylic / Clarvene

                               Polycarbonate / Dorvil

                               Prismatic Light Diffuser

                               Vantrib

                               HDPE / UHMWPE

                               PVC / PVC Foam

                               Nylon

                               HIPS

```html
<!DOCTYPE html>
<html lang="en">
<head>
<meta charset="utf-8">
<title>Tarvo Plastics Business Card</title>
<link href="https://fonts.googleapis.com/css2?family=Open+Sans:ital,wght@0,400;0,600;0,700;0,800;1,700&display=swap" rel="stylesheet">
<style>
  :root {
    --navy: #0f2a66;
    --gold: #e2a615;
    --red: #b3122a;
    --orange: #e06a1b;
    --paper: #ffffff;
    --backdrop: #e6e7ea;
    --rule: #c9cbd0;
    --ink: #3c3c3c;
  }
  * { margin: 0; padding: 0; box-sizing: border-box; }
  html, body { width: 1200px; height: 987px; overflow: hidden; }
  body {
    background: var(--backdrop);
    font-family: "Open Sans", sans-serif;
    position: relative;
  }
  .card {
    position: absolute;
    left: 220px;
    width: 760px;
    height: 464px;
    background: var(--paper);
    border-radius: 34px;
    overflow: hidden;
    box-shadow: 0 6px 18px rgba(0,0,0,0.15);
  }
  .card-front { top: 20px; }
  .card-back { top: 503px; }

  /* front */
  .front-swoosh { position: absolute; inset: 0; }
  .brand-name {
    position: absolute;
    font-weight: 800;
    color: var(--navy);
    letter-spacing: -1px;
    white-space: nowrap;
  }
  .card-front .brand-name { left: 150px; top: 52px; font-size: 76px; }
  .holder {
    position: absolute;
    left: 390px;
    top: 196px;
    font-size: 26px;
    font-weight: 700;
    color: var(--navy);
  }
  .holder .title { font-weight: 400; color: var(--orange); }
  .contact {
    position: absolute;
    left: 32px;
    right: 24px;
    top: 334px;
    color: var(--paper);
    font-size: 17px;
    line-height: 27px;
  }
  .contact li { list-style: none; display: flex; align-items: center; gap: 6px; white-space: nowrap; }
  .contact svg { width: 16px; height: 16px; flex: none; }

  /* back */
  .card-back .brand-name { left: 250px; top: 22px; font-size: 56px; }
  .tagline {
    position: absolute;
    left: 0; right: 0;
    top: 110px;
    text-align: center;
    color: var(--navy);
    font-weight: 700;
    font-style: italic;
    font-size: 19px;
    line-height: 25px;
  }
  .offer {
    position: absolute;
    top: 176px;
    color: var(--ink);
    font-size: 17px;
    line-height: 24px;
  }
  .offer h2 {
    color: var(--navy);
    font-size: 23px;
    font-weight: 700;
    margin-bottom: 4px;
  }
  .offer ul { list-style: none; }
  .offer li { position: relative; padding-left: 16px; }
  .offer li::before {
    content: "";
    position: absolute;
    left: 2px; top: 9px;
    width: 7px; height: 7px;
    border-radius: 50%;
    background: var(--orange);
  }
  .services { left: 36px; width: 390px; }
  .materials { left: 476px; width: 260px; }
  .materials .pair { display: flex; gap: 14px; }
  .divider {
    position: absolute;
    left: 448px;
    top: 180px;
    width: 1px;
    height: 240px;
    background: var(--rule);
  }
</style>
</head>
<body>

<section class="card card-front" aria-label="Business card front">
  <svg class="front-swoosh" viewBox="0 0 760 464" preserveAspectRatio="none" aria-hidden="true">
    <path d="M0,176 C220,300 500,322 760,296 L760,464 L0,464 Z" fill="var(--red)"/>
    <path d="M0,190 C220,312 500,334 760,308 L760,464 L0,464 Z" fill="var(--gold)"/>
  </svg>
  <div class="brand-name">Tarvo Plastics</div>
  <p class="holder">Your Name, <span class="title">Title</span></p>
  <ul class="contact">
    <li>Unit 4/18 Keldon Circuit Marlow Vale WA 6150</li>
    <li>PO Box 2284 Marlow Vale DC WA 6972</li>
    <li>
      <svg viewBox="0 0 16 16"><circle cx="8" cy="8" r="7.5" fill="none" stroke="#fff"/><path d="M5 4.5l1.6-.6 1 2-1 .8a5 5 0 0 0 2.2 2.2l.8-1 2 1-.6 1.6c-3 .3-6.3-3-6-6z" fill="#fff"/></svg>
      08 9471 3305
      <svg viewBox="0 0 16 16"><rect x="4.5" y="1" width="7" height="14" rx="1.5" fill="none" stroke="#fff" stroke-width="1.4"/><rect x="6" y="3" width="4" height="6" fill="#fff"/></svg>
      123-456-7890
      <svg viewBox="0 0 16 16"><rect x="2" y="6" width="12" height="8" rx="1" fill="#fff"/><rect x="4" y="2" width="8" height="5" fill="none" stroke="#fff" stroke-width="1.4"/></svg>
      08 9471 3306
    </li>
    <li>
      <svg viewBox="0 0 16 16"><circle cx="8" cy="8" r="7.5" fill="#fff"/><rect x="3.5" y="5" width="9" height="6" fill="none" stroke="var(--gold)"/><path d="M3.5 5l4.5 3.5L12.5 5" fill="none" stroke="var(--gold)"/></svg>
      sales@tarvoplastics.com.au | Norell Pty Ltd T/A Tarvo Plastics ABN: TBA
    </li>
  </ul>
</section>

<section class="card card-back" aria-label="Business card back">
  <div class="brand-name">Tarvo Plastics</div>
  <p class="tagline">The Products And Services That We Offer<br>Are Supplied From Diy To Trade &amp; Industrial Engineering Markets</p>

  <div class="offer services">
    <h2>We specialise in:</h2>
    <ul>
      <li>Cut to size panels (all shapes and sizes)</li>
      <li>Plastics fabrication &amp; Welding</li>
      <li>Custom Designs</li>
      <li>Plastic Repairs</li>
      <li>PVC Pipe Slotting &amp; PVC Pipe Threading</li>
      <li>Supplier of all types of engineering plastics and profiles</li>
    </ul>
  </div>

  <div class="divider"></div>

  <div class="offer materials">
    <h2>Including:</h2>
    <ul>
      <li>Acrylic / Clarvene</li>
      <li>Polycarbonate / Dorvil</li>
      <li>Prismatic Light Diffuser</li>
    </ul>
    <ul class="pair"><li>Vantrib</li><li>HDPE / UHMWPE</li></ul>
    <ul><li>PVC / PVC Foam</li></ul>
    <ul class="pair"><li>Nylon</li><li>HIPS</li></ul>
  </div>
</section>

</body>
</html>
```